K7 Electrical Services Ltd Web design

I require a web site for my new electrical contracting company. We are customer service orientated. Offering high value electrical installations, design and maintenance. Focused on custom residential and commercial upgrading. Lighting design and application are paramount in our company's services. Industry leading product use and integration are always on the forefront with our customer client services. As well as energy efficiency.

Target Market(s)

Homebuilders, General Contractors, Property management companies, clients, individuals,

Industry/Entity Type

Electric Company

Coding

Coded - Design and coding required

Number of Pages Required

3 page

Requirements
Must have
• Classic, modern, edgy but not trendy . Appeals to the masse.
• 3 page
• home page
• about page
• gallery page
• ability to contact from the webiste
Nice to have
• open to all types of designs that are relative to the construction industry.
• Black, Grey, metallic ice blue and deep purple colours from the logo.
Should not have
• anything cheesy with cartoon light bulb images.

```html
<!DOCTYPE html>
<html lang="en">
<head>
<meta charset="utf-8">
<title>K7 Electrical Services Ltd</title>
<link href="https://fonts.googleapis.com/css2?family=Lato:wght@400;700;900&display=swap" rel="stylesheet">
<style>
:root{
  --purple:#6b2d8e;
  --purple-soft:rgba(107,45,142,.78);
  --ink:#2b2b2b;
  --text:#3c3c3c;
  --muted:#8a8a8a;
  --line:#cfcfcf;
  --top-bg:#f4f4f4;
  --page-bg:#ffffff;
  --footer:#2f2f2f;
}
*{margin:0;padding:0;box-sizing:border-box}
html,body{width:845px;height:1200px;overflow:hidden}
body{font-family:'Lato',sans-serif;color:var(--text);background:var(--page-bg);position:relative}
.abs{position:absolute}
.header-bg{left:0;top:0;width:845px;height:170px;background:var(--top-bg)}
.accent-band{left:0;top:164px;width:845px;height:6px;background:var(--purple)}

.brand{left:91px;top:36px;display:flex;align-items:center;gap:8px}
.brand-square{width:30px;height:30px;background:var(--purple)}
.brand-name{font-weight:900;font-size:19px;color:var(--purple);letter-spacing:.5px;line-height:1.1}

.contact-bar{right:87px;top:14px;display:flex;align-items:center;gap:8px;font-size:9.5px;color:var(--muted)}
.contact-bar .icon{width:18px;height:18px;border-radius:50%;display:flex;align-items:center;justify-content:center}
.contact-bar .icon.phone{background:var(--purple)}
.contact-bar .icon.fax{background:#777}
.contact-bar .gap{width:6px}

.main-nav{left:426px;top:52px;width:338px;height:31px;background:#fff;box-shadow:0 1px 3px rgba(0,0,0,.08);display:flex;align-items:center;justify-content:space-around;font-size:11.5px;color:var(--ink)}
.main-nav a{color:inherit;text-decoration:none;position:relative}
.main-nav a.active{color:var(--purple);font-weight:700}
.main-nav .sep{width:1px;height:12px;background:var(--line)}
.nav-active-bar{left:426px;top:51px;width:63px;height:2px;background:var(--purple)}

.hero-frame{left:82px;top:118px;width:682px;height:294px;background:#fff;box-shadow:0 14px 22px -12px rgba(0,0,0,.35)}
.hero-photo{left:85px;top:120px;width:676px;height:289px;background:linear-gradient(100deg,#c9cfd3 0%,#e7eaec 35%,#d86a35 55%,#eef0f1 70%,#c3c8cc 100%)}
.hero-arrow{top:242px;width:37px;height:38px;background:var(--purple);display:flex;align-items:center;justify-content:center}
.hero-arrow.prev{left:74px}
.hero-arrow.next{left:736px}
.hero-title{left:128px;top:247px;width:310px;height:51px;background:var(--purple-soft);color:#fff;font-weight:700;font-size:18px;display:flex;align-items:center;padding-left:19px}
.hero-sub{left:154px;top:299px;width:338px;height:65px;background:rgba(255,255,255,.82);color:#222;font-size:13px;line-height:23px;padding:10px 0 0 40px}

.section-title{left:0;width:845px;text-align:center;font-size:15px;font-weight:700;color:var(--ink);text-transform:uppercase}
.about-text{left:128px;top:463px;width:590px;text-align:center;font-size:8.8px;line-height:14.6px;color:#333}

.service-card{top:531px;width:330px;height:161px;display:flex;align-items:center;justify-content:center;color:#fff;font-size:19px;font-weight:700;box-shadow:0 0 0 2px #fff,0 0 3px 2px rgba(0,0,0,.08)}
.service-card.residential{left:84px;background:linear-gradient(160deg,#7d4aa8,#5b2f86)}
.service-card.commercial{left:433px;background:linear-gradient(160deg,#7b8087,#545a63)}

.rule{height:1px;background:var(--line)}
.project-thumb{top:778px;width:156px;height:110px;box-shadow:0 0 0 2px #fff,0 0 3px 2px rgba(0,0,0,.08)}
.project-label{top:897px;width:156px;text-align:center;font-size:9.5px;color:#222;text-transform:uppercase}
.btn-more{left:388px;top:929px;width:69px;height:21px;background:var(--purple);color:#fff;font-size:9px;display:flex;align-items:center;justify-content:center;border-radius:1px}

.partner{top:1026px;width:110px;text-align:center;font-size:17px;font-weight:700;color:#6e6e6e}

.footer{left:0;top:1114px;width:845px;height:86px;background:var(--footer)}
.footer-brand{left:82px;top:1130px;font-weight:900;font-size:15px;color:#bfbfbf;line-height:1.2}
.copyright{left:78px;top:1175px;font-size:8.5px;color:#eee}
.copyright span{color:var(--purple);filter:brightness(1.6)}
.social{top:1125px;width:24px;height:24px;border-radius:50%}
.address{right:81px;top:1158px;text-align:right;font-size:8.3px;line-height:13px;color:#eee}
</style>
</head>
<body>
<div class="abs header-bg"></div>
<div class="abs accent-band"></div>

<div class="abs brand">
  <div class="brand-square"></div>
  <div class="brand-name">K7 ELECTRICAL<br>SERVICES</div>
</div>

<div class="abs contact-bar">
  <span class="icon phone"><svg width="9" height="9" viewBox="0 0 24 24"><path fill="#fff" d="M6.6 10.8a15 15 0 0 0 6.6 6.6l2.2-2.2c.3-.3.7-.4 1-.2 1.1.4 2.3.6 3.6.6.6 0 1 .4 1 1V20c0 .6-.4 1-1 1A17 17 0 0 1 3 4c0-.6.4-1 1-1h3.5c.6 0 1 .4 1 1 0 1.3.2 2.5.6 3.6.1.3 0 .7-.2 1z"/></svg></span>
  <span>Call Us :&nbsp; 1-800 555 0142</span>
  <span class="gap"></span>
  <span class="icon fax"><svg width="9" height="9" viewBox="0 0 24 24"><rect x="4" y="8" width="16" height="12" rx="2" fill="#fff"/><rect x="7" y="3" width="10" height="6" fill="#fff"/></svg></span>
  <span>Fax : 5550 1234</span>
</div>

<div class="abs nav-active-bar"></div>
<nav class="abs main-nav">
  <a class="active" href="#">Home</a><span class="sep"></span>
  <a href="#">About</a><span class="sep"></span>
  <a href="#">Services</a><span class="sep"></span>
  <a href="#">Projects</a><span class="sep"></span>
  <a href="#">Contact Us</a>
</nav>

<div class="abs hero-frame"></div>
<div class="abs hero-photo" role="img" aria-label="Engineer in orange overalls and hard hat checking an electrical switchboard"></div>
<div class="abs hero-arrow prev"><svg width="12" height="14" viewBox="0 0 12 14"><path d="M9 1 3 7l6 6" stroke="#fff" stroke-width="3" fill="none"/></svg></div>
<div class="abs hero-arrow next"><svg width="12" height="14" viewBox="0 0 12 14"><path d="m3 1 6 6-6 6" stroke="#fff" stroke-width="3" fill="none"/></svg></div>
<div class="abs hero-title">Welcome to K7 Electrical Services</div>
<div class="abs hero-sub">We Offering high value electrical installations<br>Design and maintenance.</div>

<h2 class="abs section-title" style="top:436px">About Us</h2>
<p class="abs about-text">Sit amet eget ex sed porta. Nec lobortis mauris malesuada porttitor duis eleifend felis integer turpis lacus donec lacus amet eu. Enim ac velit. Urna velit vel. Ut elit venenatis. Bibendum nulla pede aliquam vestibulum erat. Pellentesque lacus nisl sodales felis laoreet fringilla penatibus mus. Ipsum purus orci. Risus orci inceptos porta ornare mauris. Porta non nunc. Lacus at convallis vestibulum vel justo</p>

<div class="abs service-card residential" role="img" aria-label="Suburban house at dusk with purple overlay">RESIDENTIAL</div>
<div class="abs service-card commercial" role="img" aria-label="Glass office building at dusk with grey overlay">COMMERCIAL</div>

<div class="abs rule" style="left:84px;top:732px;width:292px"></div>
<h2 class="abs section-title" style="top:722px">Projects</h2>
<div class="abs rule" style="left:467px;top:732px;width:293px"></div>

<div class="abs project-thumb" style="left:85px;background:linear-gradient(180deg,#3f6fb8 0%,#7fa0cf 50%,#d99a3a 80%,#3a2a1e 100%)" role="img" aria-label="Industrial plant lit up at dusk"></div>
<div class="abs project-thumb" style="left:259px;background:linear-gradient(180deg,#2f4b78 0%,#6f7f95 45%,#9a8270 75%,#4a4440 100%)" role="img" aria-label="Retail building frontage at night"></div>
<div class="abs project-thumb" style="left:434px;background:linear-gradient(180deg,#e9e7e2 0%,#cfc8bd 55%,#3a3430 85%,#8d7a66 100%)" role="img" aria-label="Bright kitchen with island and pendant lights"></div>
<div class="abs project-thumb" style="left:607px;background:linear-gradient(180deg,#f2f3f4 0%,#d9dde0 55%,#b9bdc1 100%)" role="img" aria-label="Open plan office interior"></div>
<div class="abs project-label" style="left:85px">Project 01</div>
<div class="abs project-label" style="left:259px">Project 02</div>
<div class="abs project-label" style="left:434px">Project 03</div>
<div class="abs project-label" style="left:607px">Project 04</div>
<a class="abs btn-more">View more</a>

<div class="abs rule" style="left:84px;top:988px;width:280px"></div>
<h2 class="abs section-title" style="top:977px">Achievements</h2>
<div class="abs rule" style="left:484px;top:988px;width:276px"></div>

<div class="abs partner" style="left:85px">Flooris</div>
<div class="abs partner" style="left:229px">Northwave</div>
<div class="abs partner" style="left:370px">VOLTRA</div>
<div class="abs partner" style="left:511px">Campus Union</div>
<div class="abs partner" style="left:653px">Kestrel</div>

<svg class="abs" style="left:0;top:1086px" width="845" height="30" viewBox="0 0 845 30">
  <polygon points="64,28 416,4 768,28 768,30 416,8 64,30" fill="#6b2d8e"/>
  <polygon points="64,30 416,8 768,30" fill="#f4f4f4"/>
</svg>
<footer class="abs footer"></footer>
<div class="abs footer-brand">K7 ELECTRICAL<br>SERVICES</div>
<div class="abs copyright">Copyright © 2018 <span>K7 Electrical Services</span> All Rights Reserved.</div>
<div class="abs social" style="left:706px;background:#1f5fa8" aria-label="Social profile"></div>
<div class="abs social" style="left:737px;background:#19b3d6" aria-label="Social profile"></div>
<div class="abs address">
  <svg width="7" height="9" viewBox="0 0 12 16" style="vertical-align:-1px;margin-right:5px"><path fill="#fff" d="M6 0a6 6 0 0 0-6 6c0 4.5 6 10 6 10s6-5.5 6-10a6 6 0 0 0-6-6zm0 8.5A2.5 2.5 0 1 1 6 3.5a2.5 2.5 0 0 1 0 5z"/></svg>14 Harlow Crescent #03-08, Vantage Industrial Building.<br>Eastport 40512
</div>
</body>
</html>
```